Business card design for my company.
I would like the card's background colour to be black. You can also see our web site to get an idea of our brand. https://www.tmwhomecrafting.com.au/
- Name
- Email

```html
<!DOCTYPE html>
<html lang="en">
<head>
<meta charset="UTF-8">
<title>TMW Home Crafting – Business Card</title>
<link rel="stylesheet" href="https://fonts.googleapis.com/css2?family=Montserrat:wght@400;700;800&display=swap">
<style>
  :root {
    --stage: #161616;
    --card-black: #1f1f1f;
    --pattern-dark: #1a1a1a;
    --pattern-light: #2a2a2a;
    --brand-green: #14994a;
    --white: #ffffff;
  }
  * { margin: 0; padding: 0; box-sizing: border-box; }
  html, body {
    width: 1200px; height: 900px; overflow: hidden;
    background: var(--stage);
    font-family: "Montserrat", sans-serif;
  }
  .canvas { position: relative; width: 1200px; height: 900px; }

  .card {
    position: absolute;
    width: 620px; height: 354px;
    border-radius: 18px;
    overflow: hidden;
    background: var(--card-black);
    box-shadow: 0 18px 40px rgba(0,0,0,.55);
  }

  /* Back side */
  .card-back { left: 140px; top: 70px; }
  .card-back .brand-pattern {
    position: absolute; inset: 0;
    background: linear-gradient(135deg, var(--pattern-dark) 0%, var(--pattern-light) 100%);
  }
  .card-back .back-mark {
    position: absolute; right: 70px; top: 150px;
    display: flex; align-items: center; gap: 8px;
    color: var(--white); font-weight: 700; font-size: 17px;
  }
  .mark-square { width: 12px; height: 12px; background: var(--brand-green); }

  /* Front side */
  .card-front { left: 440px; top: 476px; }
  .card-front .green-band { position: absolute; inset: 0; }
  .front-mark {
    position: absolute; left: 46px; top: 64px;
    display: flex; align-items: center; gap: 12px;
    color: var(--white); font-weight: 800; font-size: 30px;
    line-height: 1.05;
  }
  .front-mark .mark-square { width: 22px; height: 22px; }

  .contact {
    position: absolute; right: 34px; top: 118px;
    text-align: right; color: var(--white);
  }
  .contact .person-name { font-weight: 800; font-size: 24px; letter-spacing: .5px; }
  .contact .person-role { font-weight: 400; font-size: 14px; margin-bottom: 14px; }
  .contact .line {
    display: flex; justify-content: flex-end; align-items: center; gap: 8px;
    font-size: 14px; line-height: 22px;
  }
  .contact svg { width: 12px; height: 12px; fill: var(--white); }
</style>
</head>
<body>
<main class="canvas">

  <section class="card card-back">
    <div class="brand-pattern" role="img" aria-label="Repeating faint brand pattern in dark greys"></div>
    <div class="back-mark"><span class="mark-square"></span>TMW Home Crafting</div>
  </section>

  <section class="card card-front">
    <svg class="green-band" viewBox="0 0 620 354" preserveAspectRatio="none">
      <polygon points="0,290 505,48 612,70 620,74 620,354 0,354" fill="var(--brand-green)"/>
    </svg>

    <div class="front-mark"><span class="mark-square"></span>TMW Home<br>Crafting</div>

    <div class="contact">
      <div class="person-name">DANA WHITFIELD</div>
      <div class="person-role">CEO/Founder</div>
      <div class="line">555-014-2738
        <svg viewBox="0 0 24 24"><path d="M6.6 10.8a15.1 15.1 0 0 0 6.6 6.6l2.2-2.2a1 1 0 0 1 1-.25 11.4 11.4 0 0 0 3.6.57 1 1 0 0 1 1 1V20a1 1 0 0 1-1 1A17 17 0 0 1 3 4a1 1 0 0 1 1-1h3.5a1 1 0 0 1 1 1c0 1.25.2 2.45.57 3.57a1 1 0 0 1-.25 1z"/></svg>
      </div>
      <div class="line">info@tmwhomecrafting.com.au
        <svg viewBox="0 0 24 24"><path d="M2 5h20v14H2z M2 5l10 8 10-8" fill="none" stroke="#fff" stroke-width="2"/></svg>
      </div>
      <div class="line">www.tmwhomecrafting.com.au
        <svg viewBox="0 0 24 24"><g fill="none" stroke="#fff" stroke-width="2"><circle cx="12" cy="12" r="10"/><path d="M2 12h20M12 2c3 3 3 17 0 20M12 2c-3 3-3 17 0 20"/></g></svg>
      </div>
    </div>
  </section>

</main>
</body>
</html>
```